Chimney Service company needs new business card design

We need a updated business card with our new logo added. We provide a full range of chimney services throughout Vermont and New Hampshire. The business card will be one sided and color. Attached is our current business card another document showing all the information we would like on the card.
We dont like a lot of flashy colors.... here is a link to our website to get an idea of our branding www.flueguardianvt.example

Target Market(s)

homeowners

Industry/Entity Type

Business

Contact Information for Business Card

See attached sheet for content.

Font styles to use
Serif
Sans Serif

Requirements
Must have
• all information provided on separate sheet
Should not have
• Additional information that may clogg up design

```html
<!DOCTYPE html>
<html lang="en">
<head>
<meta charset="utf-8">
<title>Flue Guardian – Business Card</title>
<link href="https://fonts.googleapis.com/css2?family=Cinzel:wght@400;500&family=Montserrat:wght@400&display=swap" rel="stylesheet">
<style>
  :root {
    --page: #e6e4e0;
    --card-white: #f7f7f6;
    --band: #3a3b3d;
    --ink: #4a4b4d;
    --accent: #a3202a;
    --light-text: #eeeeee;
  }
  * { box-sizing: border-box; margin: 0; padding: 0; }
  html, body { width: 1200px; height: 1022px; overflow: hidden; }
  body { background: var(--page); position: relative; }

  .card {
    position: absolute; left: 100px; top: 225px;
    width: 1000px; height: 572px;
    background: var(--card-white);
    box-shadow: 0 6px 24px rgba(0,0,0,.18);
    overflow: hidden;
  }
  .card__band {
    position: absolute; left: 0; right: 0; top: 318px; bottom: 0;
    background: var(--band);
  }
  .card__rule {
    position: absolute; left: 0; right: 0; top: 312px; height: 3px;
    background: var(--accent);
  }

  .brand-mark {
    position: absolute; left: 60px; top: 118px; width: 320px;
    display: flex; align-items: center; gap: 16px;
  }
  .brand-mark__square { width: 38px; height: 38px; background: var(--accent); flex: none; }
  .brand-mark__name {
    font-family: "Cinzel", serif; font-weight: 500; font-size: 30px;
    color: var(--ink); line-height: 1.1; white-space: nowrap;
  }

  .company {
    position: absolute; right: 60px; top: 70px; text-align: right;
    font-family: "Cinzel", serif; color: var(--ink);
  }
  .company__name { font-size: 54px; font-weight: 400; letter-spacing: 2px; line-height: 1; white-space: nowrap; }
  .company__line { height: 2px; background: var(--ink); margin: 12px 0 8px auto; width: 100%; }
  .company__since {
    display: flex; align-items: center; justify-content: flex-end; gap: 14px;
    font-size: 22px; letter-spacing: 2px;
  }
  .company__since::before { content: ""; width: 150px; height: 2px; background: var(--ink); }

  .services {
    position: absolute; left: 60px; top: 350px; list-style: none;
    font-family: "Cinzel", serif; font-size: 21px; color: var(--light-text);
    line-height: 1.55; letter-spacing: .5px; white-space: nowrap;
  }
  .services li::before { content: "•"; margin-right: 12px; }

  .contact {
    position: absolute; right: 60px; top: 385px; list-style: none;
    font-family: "Montserrat", sans-serif; font-size: 22px; color: var(--light-text);
    line-height: 1.75; white-space: nowrap;
  }
  .contact li { display: flex; align-items: center; gap: 14px; }
  .contact svg { width: 18px; height: 18px; flex: none; }
</style>
</head>
<body>
  <article class="card">
    <div class="card__band"></div>
    <div class="card__rule"></div>

    <div class="brand-mark">
      <span class="brand-mark__square"></span>
      <span class="brand-mark__name">Flue Guardian</span>
    </div>

    <header class="company">
      <h1 class="company__name">FLUE GUARDIAN</h1>
      <div class="company__line"></div>
      <div class="company__since">INC 2004</div>
    </header>

    <ul class="services">
      <li>Full Masonry Services</li>
      <li>Historic Chimney Restoration</li>
      <li>Stainless Steel Liners</li>
      <li>Guild Certified Chimney Sweep</li>
      <li>Fully Insured • Free Estimates</li>
    </ul>

    <ul class="contact">
      <li>
        <svg viewBox="0 0 24 24" fill="#eeeeee"><path d="M6.6 10.8a15 15 0 0 0 6.6 6.6l2.2-2.2a1 1 0 0 1 1-.25 11.4 11.4 0 0 0 3.6.57 1 1 0 0 1 1 1V20a1 1 0 0 1-1 1A17 17 0 0 1 3 4a1 1 0 0 1 1-1h3.5a1 1 0 0 1 1 1c0 1.25.2 2.45.57 3.57a1 1 0 0 1-.25 1z"/></svg>
        802-555-0147
      </li>
      <li>
        <svg viewBox="0 0 24 24" fill="none" stroke="#eeeeee" stroke-width="2"><rect x="3" y="5" width="18" height="14" rx="1"/><path d="M3 6l9 7 9-7"/></svg>
        info@flueguardianvt.example
      </li>
      <li>
        <svg viewBox="0 0 24 24" fill="none" stroke="#eeeeee" stroke-width="2"><circle cx="12" cy="12" r="9"/><path d="M3 12h18M12 3c3 3 3 15 0 18M12 3c-3 3-3 15 0 18"/></svg>
        www.flueguardianvt.example
      </li>
    </ul>
  </article>
</body>
</html>
```